RW Holloway LLC Business Card - Civil Engineering & Consulting Firm

We need a Business Card that is elegant, and masculine.  It is our Professional Civil Engineering & Consulting Company located in San Antonio TX (Not s construction or builder firm- no gears & no tool images please). We provide civil engineering services including  commercial site plans, grading and drainage plans, utility plans, hydraulics and hydrology, land planning, utility coordination, and other general civil engineering services related to commercial and residential development.
We have 2 existing Logos. We would like to convey reliability, strength, trustworthiness and attention to detail.  Blues and orange tones as per logo We are OK with the use of a darker blue in the mix.  We have 2 logo versions - Full Company Name Logo to go on the back of card, & Small Icon Logo for the front w/ personal Info.

Target Market(s)
Architects, Real Estate Developers, Other Strctural Engineers, Surveyers, General Contractors
Industry/Entity Type
Professional Civil Engineering
Contact Information for Business Card
Name, Position, Address, Cell & Office #, email, and company website
Font styles to use
Other font styles liked:
- Avian
Requirements
Should not have
- No Tools, No Gears, no Cranes, or Construction Equipment.

```html
<!DOCTYPE html>
<html lang="en">
<head>
<meta charset="UTF-8">
<title>RW Holloway LLC – Business Card</title>
<link rel="stylesheet" href="https://fonts.googleapis.com/css2?family=Questrial&family=Montserrat:wght@700&display=swap">
<style>
  :root {
    --backdrop: #1e1f21;
    --navy: #03223f;
    --sky: #7aaddc;
    --orange: #f39322;
    --white: #ffffff;
  }
  * { box-sizing: border-box; margin: 0; padding: 0; }
  html, body {
    width: 1200px;
    height: 874px;
    overflow: hidden;
    background: var(--backdrop);
  }
  .canvas {
    position: relative;
    width: 1200px;
    height: 874px;
  }
  .card {
    position: absolute;
    left: 290px;
    width: 620px;
    height: 354px;
    background: var(--navy);
    font-family: "Questrial", sans-serif;
  }
  .card--back { top: 62px; }
  .card--front {
    top: 458px;
    border-top: 12px solid var(--sky);
    border-left: 12px solid var(--sky);
    border-right: 12px solid var(--orange);
    border-bottom: 12px solid var(--orange);
  }

  .brand-name {
    position: absolute;
    left: 0;
    right: 0;
    top: 150px;
    text-align: center;
    font-size: 46px;
    letter-spacing: 5px;
    color: var(--sky);
  }

  .holder {
    position: absolute;
    left: 52px;
    top: 58px;
  }
  .holder__name {
    font-family: "Montserrat", sans-serif;
    font-weight: 700;
    font-size: 25px;
    color: var(--orange);
    letter-spacing: 0.5px;
  }
  .holder__role {
    font-size: 17px;
    color: var(--sky);
    margin-top: 1px;
  }
  .contact {
    list-style: none;
    margin-top: 18px;
  }
  .contact__item {
    display: flex;
    align-items: center;
    gap: 9px;
    font-size: 17px;
    color: var(--white);
    line-height: 24px;
  }
  .contact__icon { width: 12px; height: 12px; flex: none; }
  .address {
    font-style: normal;
    font-size: 17px;
    color: var(--white);
    line-height: 22px;
    margin-top: 12px;
  }
  .front-mark {
    position: absolute;
    right: 40px;
    top: 132px;
    font-size: 22px;
    letter-spacing: 2px;
    color: var(--sky);
  }
</style>
</head>
<body>
<main class="canvas">
  <section class="card card--back" aria-label="Card back">
    <p class="brand-name">RW HOLLOWAY LLC</p>
  </section>

  <section class="card card--front" aria-label="Card front">
    <div class="holder">
      <h1 class="holder__name">DANIEL REYES</h1>
      <p class="holder__role">President</p>
      <ul class="contact">
        <li class="contact__item">
          <svg class="contact__icon" viewBox="0 0 12 12"><path d="M2 1l2.5 0 1 3-1.5 1a7 7 0 0 0 3 3l1-1.5 3 1V10a1.5 1.5 0 0 1-1.5 1.5C5 11.5.5 7 .5 2.5A1.5 1.5 0 0 1 2 1z" fill="var(--orange)"/></svg>
          210-555-0147
        </li>
        <li class="contact__item">
          <svg class="contact__icon" viewBox="0 0 12 12"><rect x="2.5" y="0.5" width="7" height="11" rx="1.2" fill="none" stroke="var(--orange)" stroke-width="1.4"/></svg>
          210-555-0192
        </li>
        <li class="contact__item">
          <svg class="contact__icon" viewBox="0 0 12 12"><rect x="0.5" y="2" width="11" height="8" fill="var(--orange)"/><path d="M0.5 2l5.5 4.5L11.5 2" fill="none" stroke="var(--navy)" stroke-width="1"/></svg>
          dreyes@rwholloway.com
        </li>
        <li class="contact__item">
          <svg class="contact__icon" viewBox="0 0 12 12"><circle cx="6" cy="6" r="5.5" fill="var(--orange)"/><path d="M6 .5v11M.5 6h11" stroke="var(--navy)" stroke-width="0.9"/></svg>
          www.rwholloway.com
        </li>
      </ul>
      <address class="address">4120 Cedar Bend Drive, San Antonio<br>Texas 78209</address>
    </div>
    <p class="front-mark">RW HOLLOWAY</p>
  </section>
</main>
</body>
</html>
```